Meadowfield Baptist Church Banner Design

Designing 6 banners (3 + 3 that will hang on opposite sides of our auditorium) that are 10 feet long by 4 feet wide.

Use our branding guide - specifically item 4 (vertical logo) and item 5 (icon logo).

Design elements found in our KINDLE booklet, we would like to see designs that utilize the white, green and blue colour palettes but NOT the grey. Other colours may be incorporated (e.g. coral).

We are looking for 3 banner designs that would match on either side of the auditorium, the first banner incorporating the word "TRUTH", the second incorporating the word "LOVE", and the third incorporating the word "MISSION".

We interested in incorporating graphics such as trees or outdoor themes.

Font styles to use
Other font styles liked:
• Montserrat

Colors
34a7d7
00a990
f47c35

Requirements
Must have
• Banner Type #1 include the word "TRUTH"
Banner Type #2 include the word "LOVE"
Banner Type #3 include the word "MISSION"

Colour scheme must include CMYK 54 / 5 / 16 / 0 (which is available in the branding guide.) We have selected the three colours, included below in the brief.

From the branding guide - utilize #5 (icon) for the banner.

UPDATE: After reviewing the initial submissions, we are asking for designs that ONLY incorporate #5 - the ICON logo for the banners.
Nice to have
• It would be nice to have some creativity with the colour ... though a more minimalistic style is preferred.

Graphic adaptations such as trees in the background would be of interest.
Should not have
• Colour scheme should not be gray scale.

The banners should NOT be too busy.

Scripture verses (written out) are not necessary.

```html
<!DOCTYPE html>
<html lang="en">
<head>
<meta charset="utf-8">
<title>Mission Banner – Meadowfield Baptist Church</title>
<link rel="stylesheet" href="https://fonts.googleapis.com/css2?family=Montserrat:wght@700&family=Tinos:ital@1&display=swap">
<style>
  :root {
    --banner-blue: #34a7d7;
    --text-white: #ffffff;
    --brand-tint: #cfe9f6;
  }
  html, body {
    margin: 0;
    padding: 0;
    width: 1200px;
    height: 2710px;
    overflow: hidden;
    background: var(--banner-blue);
  }
  .banner {
    position: relative;
    width: 1200px;
    height: 2710px;
    background: var(--banner-blue);
    color: var(--text-white);
    overflow: hidden;
  }
  .banner__word {
    position: absolute;
    left: 0;
    right: 0;
    top: 560px;
    margin: 0;
    text-align: center;
    font-family: "Montserrat", sans-serif;
    font-weight: 700;
    font-size: 284px;
    line-height: 1;
    letter-spacing: -6px;
  }
  .definition {
    position: absolute;
    left: 162px;
    top: 1010px;
    width: 960px;
    font-family: "Tinos", "Times New Roman", serif;
    font-style: italic;
    font-weight: 400;
  }
  .definition__class {
    margin: 0 0 90px;
    font-size: 74px;
    line-height: 1;
  }
  .definition__text {
    margin: 0;
    font-size: 62px;
    line-height: 76px;
  }
  .brand-mark {
    position: absolute;
    left: 162px;
    bottom: 150px;
    margin: 0;
    font-family: "Montserrat", sans-serif;
    font-weight: 700;
    font-size: 64px;
    line-height: 1.15;
    color: var(--brand-tint);
  }
</style>
</head>
<body>
  <main class="banner">
    <h1 class="banner__word">mission</h1>

    <section class="definition">
      <p class="definition__class">noun</p>
      <p class="definition__text">1. the vocation or calling of a<br>religious organization, espe-<br>cially a Christian one, to go out<br>into the world and spread its<br>faith.</p>
    </section>

    <p class="brand-mark">Meadowfield<br>Baptist Church</p>
  </main>
</body>
</html>
```